Employee Benefits and Insurance Consulting

We are an existing company with over 30 years experience but are changing our name. We would like a simple design with grey tones.

Industry/Entity Type

Insurance

Contact Information for Business Card

Marlow Benefits Consulting
Gerald P Hollins CEO
5172 Brackenridge Road
Brackenton, TN 37790
gerald@marlowbenefits-example.com
865-412-5593 - O
865-247-3861 - C

```html
<!DOCTYPE html>
<html lang="en">
<head>
<meta charset="utf-8">
<title>Marlow Benefits Consulting – Business Card</title>
<link rel="stylesheet" href="https://fonts.googleapis.com/css2?family=Roboto:wght@400;700&display=swap">
<style>
  :root {
    --navy: #174a7e;
    --grey-bar: #9a9a9a;
    --grey-text: #6b6b6b;
    --ink: #5a5a5a;
    --card: #ffffff;
    --backdrop: #e8e8e8;
  }
  * { box-sizing: border-box; margin: 0; padding: 0; }
  html, body {
    width: 1200px; height: 1000px; overflow: hidden;
    background: var(--backdrop);
    font-family: "Roboto", Arial, sans-serif;
  }
  .business-card {
    position: absolute;
    left: 100px; top: 202px;
    width: 1000px; height: 596px;
    background: var(--card);
    box-shadow: 0 2px 6px rgba(0,0,0,0.15);
  }
  .brand {
    position: absolute;
    left: 48px; top: 80px;
    width: 420px;
    text-align: center;
  }
  .brand-mark {
    display: block;
    width: 72px; height: 72px;
    margin: 0 auto 70px;
    background: var(--navy);
  }
  .brand-name {
    color: var(--navy);
    font-weight: 400;
    font-size: 36px;
    line-height: 1.2;
    letter-spacing: 1px;
  }
  .contact-list {
    position: absolute;
    left: 48px; top: 390px;
    list-style: none;
    color: var(--ink);
    font-size: 23px;
    line-height: 35px;
  }
  .contact-list li { display: flex; align-items: center; }
  .contact-icon { width: 22px; height: 22px; margin-right: 10px; fill: var(--navy); }
  .address {
    position: absolute;
    left: 48px; top: 498px;
    font-style: normal;
    color: var(--ink);
    font-size: 23px;
    line-height: 31px;
  }
  .person {
    position: absolute;
    left: 540px; top: 375px;
    width: 430px;
    text-align: center;
  }
  .person-name {
    color: var(--navy);
    font-weight: 700;
    font-size: 33px;
    letter-spacing: 0.5px;
  }
  .person-title {
    color: var(--grey-text);
    font-size: 25px;
    margin-top: 2px;
  }
  .footer-bar {
    position: absolute; bottom: 0; height: 20px;
  }
  .footer-bar--navy { left: 0; width: 495px; background: var(--navy); }
  .footer-bar--grey { left: 503px; right: 0; background: var(--grey-bar); }
</style>
</head>
<body>
  <article class="business-card">
    <header class="brand">
      <span class="brand-mark"></span>
      <h1 class="brand-name">Marlow Benefits Consulting</h1>
    </header>

    <ul class="contact-list">
      <li>
        <svg class="contact-icon" viewBox="0 0 24 24" aria-hidden="true"><path d="M3 9c0-3 4-5 9-5s9 2 9 5v2h-5V9c-1-.6-2.5-1-4-1s-3 .4-4 1v2H3z M6 13h12l2 7H4z M12 15a2 2 0 1 0 0 4a2 2 0 0 0 0-4z"/></svg>
        865-412-5593
      </li>
      <li>
        <svg class="contact-icon" viewBox="0 0 24 24" aria-hidden="true"><path d="M7 2h10a1 1 0 0 1 1 1v18a1 1 0 0 1-1 1H7a1 1 0 0 1-1-1V3a1 1 0 0 1 1-1zm1 3v8h8V5zm1 10v2h2v-2zm4 0v2h2v-2zm-4 3v2h2v-2zm4 0v2h2v-2z"/></svg>
        865-247-3861
      </li>
      <li>
        <svg class="contact-icon" viewBox="0 0 24 24" aria-hidden="true"><path d="M2 6h20v12H2z" fill="var(--navy)"/><path d="M2 6l10 7l10-7" fill="none" stroke="#fff" stroke-width="1.5"/></svg>
        gerald@marlowbenefits-example.com
      </li>
    </ul>

    <address class="address">
      5172 Brackenridge Road<br>
      Brackenton, TN 37790
    </address>

    <div class="person">
      <p class="person-name">GERALD P HOLLINS</p>
      <p class="person-title">CEO</p>
    </div>

    <div class="footer-bar footer-bar--navy"></div>
    <div class="footer-bar footer-bar--grey"></div>
  </article>
</body>
</html>
```